Banner Pop Up Opt In Form REDESIGNS - SLEEK BLACK LOOK

Please redesign banners attached.

I am looking for a very sleek look....I do not like this collage of images on these current designs. Please keep all content same but use images that pop.

I have an acccount at www.pixvane-example.com or you can use your own images.

I like black background for somereason because it looks very sleek....but these designs should pop , build trust and credibility and have easy opt in form....SLEEK AND MODERN LOOK is what im looking for....

Target Market(s)

Consumers on websites

Requirements
Must have
• Please redesign banners attached.

Nice to have

Should not have

```html
<!DOCTYPE html>
<html lang="en">
<head>
<meta charset="UTF-8">
<title>Newsletter Opt-In Banner</title>
<link rel="stylesheet" href="https://fonts.googleapis.com/css2?family=Open+Sans:wght@300;400;600;700&display=swap">
<style>
  :root {
    --panel-dark: #1f1f1f;
    --field-bg: #4a4a4a;
    --field-text: #a9a9a9;
    --button-bg: #000000;
    --button-text: #8a8a8a;
    --gold: #936b2d;
    --gold-text: #e2cfae;
    --white: #ffffff;
    --muted: #a8a8a8;
    --lagoon-light: #8fe0d8;
    --lagoon-mid: #3fb8b3;
    --lagoon-deep: #137f86;
  }
  * { box-sizing: border-box; margin: 0; padding: 0; }
  html, body {
    width: 1200px;
    height: 1031px;
    overflow: hidden;
    background: var(--panel-dark);
    font-family: "Open Sans", Arial, sans-serif;
  }
  .banner {
    position: relative;
    width: 1200px;
    height: 1031px;
  }
  .offer-panel {
    position: absolute;
    left: 0; top: 0;
    width: 717px; height: 1031px;
    background: var(--panel-dark);
  }
  .accent-bar {
    position: absolute;
    left: 187px;
    width: 337px;
    height: 14px;
    background: var(--gold);
  }
  .accent-bar--top { top: 0; }
  .accent-bar--bottom { bottom: 0; }
  .headline {
    position: absolute;
    left: 0; top: 82px;
    width: 717px;
    text-align: center;
    color: var(--white);
    font-weight: 300;
    font-size: 71px;
    line-height: 84px;
    letter-spacing: 1px;
  }
  .subhead {
    position: absolute;
    left: 0; top: 330px;
    width: 717px;
    text-align: center;
    color: var(--muted);
    font-weight: 600;
    font-size: 27px;
    line-height: 35.5px;
    letter-spacing: 1px;
  }
  .certificate {
    position: absolute;
    left: 0; top: 500px;
    width: 717px;
    text-align: center;
    color: var(--white);
    font-weight: 700;
    font-size: 33px;
    letter-spacing: 1.5px;
  }
  .optin-form {
    position: absolute;
    left: 68px; top: 632px;
    width: 578px;
  }
  .field {
    display: block;
    width: 578px;
    height: 85px;
    margin-bottom: 8px;
    padding: 0 28px;
    border: none;
    background: var(--field-bg);
    color: var(--white);
    font-family: "Open Sans", Arial, sans-serif;
    font-weight: 300;
    font-size: 30px;
    outline: none;
  }
  .field::placeholder { color: var(--field-text); }
  .submit-button {
    display: block;
    width: 578px;
    height: 85px;
    margin-top: 9px;
    border: none;
    background: var(--button-bg);
    color: var(--button-text);
    font-family: "Open Sans", Arial, sans-serif;
    font-weight: 700;
    font-size: 33px;
    letter-spacing: 1px;
  }
  .hero-image {
    position: absolute;
    left: 717px; top: 0;
    width: 483px; height: 817px;
    background:
      radial-gradient(ellipse 70% 45% at 62% 48%, rgba(255,255,255,0.28), rgba(255,255,255,0) 70%),
      linear-gradient(160deg, var(--lagoon-light) 0%, var(--lagoon-mid) 50%, var(--lagoon-deep) 100%);
  }
  .redeem-note {
    position: absolute;
    left: 717px; top: 817px;
    width: 483px; height: 214px;
    background: var(--gold);
    color: var(--gold-text);
    text-align: center;
    font-size: 21px;
    line-height: 28px;
    padding-top: 58px;
  }
</style>
</head>
<body>
<div class="banner">
  <section class="offer-panel">
    <div class="accent-bar accent-bar--top"></div>
    <h1 class="headline">WANT A<br>GREAT OFFER?</h1>
    <p class="subhead">SUBSCRIBE TO OUR<br>NEWSLETTER AND<br>RECEIVE A COMPLIMENTARY</p>
    <p class="certificate">$300 RESTAURANT CERTIFICATE</p>
    <form class="optin-form">
      <input class="field" type="text" placeholder="Name">
      <input class="field" type="email" placeholder="Email">
      <input class="field" type="tel" placeholder="Phone">
      <button class="submit-button" type="button">SUBMIT</button>
    </form>
    <div class="accent-bar accent-bar--bottom"></div>
  </section>

  <div class="hero-image" role="img" aria-label="Single vivid aerial photo of a paddleboarder gliding over clear turquoise lagoon water"></div>

  <p class="redeem-note">We will send an email<br>and text message with the offer<br>and instructions on how to redeem.</p>
</div>
</body>
</html>
```